Automotive spring company needs banner for website

Banner dimensions: 3840 x 880 pixels
Banner need to be consistent with our branding (logo, stationary, colors, fonts, message).
People images should show happiness and it is preferable those people are in or around a car unless it ties into one of the 3 quotes in the must haves below.
Use color blue #4885ed
and gold color #f7d105
Minimal, strong, clean, & tech

35-55 male and female

Auto Repair

• Clickable element for "Shop" or "Make an Appointment"
• "25 Years of Customer Satisfaction" or
• "Get it Done Right by Specialist" or
• "Peace of Mind National Warranty"
• Use our font, Eurostile and/or complimentary font paring

```html
<!DOCTYPE html>
<html lang="en">
<head>
<meta charset="UTF-8">
<title>Coilpoint Website Banner</title>
<link href="https://fonts.googleapis.com/css2?family=Krona+One&display=swap" rel="stylesheet">
<style>
  :root {
    --page-bg: #f1f1f1;
    --brand-blue: #4885ed;
    --brand-gold: #f7d105;
    --text-white: #f4f6fb;
    --rule: rgba(255, 255, 255, 0.55);
    --photo-warm: #b08a5c;
    --photo-dark: #4a3a24;
    --photo-teal: #2a8fb8;
  }
  html, body {
    margin: 0;
    width: 1200px;
    height: 1200px;
    overflow: hidden;
    background: var(--page-bg);
  }
  .banner {
    position: absolute;
    left: 16px;
    top: 466px;
    width: 1166px;
    height: 266px;
    overflow: hidden;
    box-shadow: 0 1px 4px rgba(0, 0, 0, 0.25);
    background: var(--brand-blue);
  }
  .banner__photo {
    position: absolute;
    left: 0;
    top: 0;
    width: 690px;
    height: 266px;
    background:
      radial-gradient(ellipse at 30% 20%, #8a7a55 0%, transparent 55%),
      linear-gradient(180deg, var(--photo-dark) 0%, var(--photo-warm) 45%, var(--photo-teal) 62%, #3a3a3a 100%);
  }
  .banner__edge {
    position: absolute;
    left: 0;
    top: 0;
    width: 1166px;
    height: 266px;
  }
  .banner__message {
    position: absolute;
    left: 808px;
    top: 0;
    width: 320px;
    height: 266px;
    text-align: center;
    font-family: "Krona One", sans-serif;
  }
  .banner__rule {
    position: absolute;
    left: 0;
    width: 320px;
    height: 1px;
    background: linear-gradient(90deg, transparent, var(--rule) 20%, var(--rule) 80%, transparent);
  }
  .banner__rule--top { top: 30px; }
  .banner__rule--bottom { top: 174px; }
  .headline {
    position: absolute;
    top: 44px;
    left: -20px;
    right: -20px;
    margin: 0;
    font-size: 31px;
    line-height: 40px;
    font-weight: 400;
    color: var(--text-white);
    letter-spacing: 0.5px;
  }
  .headline__years { color: var(--brand-gold); display: block; }
  .headline__line { display: block; }
  .brand-name {
    position: absolute;
    top: 198px;
    left: 0;
    right: 0;
    font-size: 26px;
    line-height: 32px;
    color: var(--brand-gold);
    letter-spacing: 1px;
  }
</style>
</head>
<body>
  <section class="banner" aria-label="Website banner">
    <div class="banner__photo" role="img" aria-label="Photo of two happy women leaning out of a blue car in a sunny wooded setting, giving a high five"></div>
    <svg class="banner__edge" viewBox="0 0 1166 266" aria-hidden="true">
      <g fill="#3f7ee8">
        <rect x="612" y="2" width="170" height="36" rx="18"/>
        <rect x="612" y="48" width="166" height="40" rx="20"/>
        <rect x="612" y="98" width="170" height="42" rx="21"/>
        <rect x="612" y="150" width="168" height="40" rx="20"/>
        <rect x="612" y="200" width="170" height="40" rx="20"/>
        <rect x="612" y="246" width="166" height="30" rx="15"/>
      </g>
      <rect x="640" y="0" width="526" height="266" fill="var(--brand-blue)"/>
      <g fill="var(--brand-blue)">
        <rect x="612" y="8" width="60" height="30" rx="15"/>
        <rect x="612" y="52" width="60" height="34" rx="17"/>
        <rect x="612" y="104" width="60" height="34" rx="17"/>
        <rect x="612" y="154" width="60" height="34" rx="17"/>
        <rect x="612" y="204" width="60" height="34" rx="17"/>
        <rect x="612" y="248" width="60" height="26" rx="13"/>
      </g>
    </svg>
    <div class="banner__message">
      <div class="banner__rule banner__rule--top"></div>
      <h1 class="headline">
        <span class="headline__years">25 Years</span>
        <span class="headline__line">of Customer</span>
        <span class="headline__line">Satisfaction</span>
      </h1>
      <div class="banner__rule banner__rule--bottom"></div>
      <div class="brand-name">COILPOINT</div>
    </div>
  </section>
</body>
</html>
```